One of a kind service business!

We are the only ocean freight auditing company in the entire world that does what we do. We provide a innovative service in auditing our clients invoices for billing errors as it relates to the import and export of their products anywhere in the world. We'd like to retain the current logo - but we are open to any interesting concepts that can complete the card.

Target Market(s)

C-Level and Senior Financial executives

Industry/Entity Type

Auditing

Requirements
Must have

• ONE SIDED ONLY
Should not have
• no cartoonish images

```html
<!DOCTYPE html>
<html lang="en">
<head>
<meta charset="utf-8">
<title>Tidewater Review – Business Card</title>
<link href="https://fonts.googleapis.com/css2?family=Questrial&display=swap" rel="stylesheet">
<style>
  :root {
    --backdrop: #e6e8e4;
    --card-dark: #3a393b;
    --panel-white: #ffffff;
    --ink: #3f3e40;
    --accent-blue: #6cc3e8;
    --logo-tint: #9fd8f0;
  }
  * { margin: 0; padding: 0; box-sizing: border-box; }
  html, body {
    width: 1200px;
    height: 898px;
    overflow: hidden;
    background: var(--backdrop);
    font-family: "Questrial", "Century Gothic", sans-serif;
  }
  .card {
    position: absolute;
    left: 150px;
    top: 166px;
    width: 900px;
    height: 566px;
    background: var(--card-dark);
    box-shadow: 0 6px 24px rgba(0,0,0,0.18);
  }
  .brand {
    position: absolute;
    left: 61px;
    top: 250px;
    display: flex;
    align-items: center;
    gap: 12px;
  }
  .brand-square {
    width: 22px;
    height: 22px;
    background: var(--accent-blue);
  }
  .brand-name {
    font-size: 34px;
    color: var(--logo-tint);
    letter-spacing: 0.5px;
    white-space: nowrap;
  }
  .contact-panel {
    position: absolute;
    left: 423px;
    top: 126px;
    right: 0;
    bottom: 0;
    background: var(--panel-white);
    color: var(--ink);
  }
  .person-name {
    position: absolute;
    left: 18px;
    top: 18px;
    font-size: 33px;
    letter-spacing: 0.5px;
    color: #333234;
    -webkit-text-stroke: 0.6px #333234;
  }
  .person-title {
    position: absolute;
    left: 201px;
    top: 64px;
    font-size: 20px;
    letter-spacing: 1px;
    color: var(--accent-blue);
  }
  .details {
    position: absolute;
    left: 18px;
    top: 164px;
    list-style: none;
    font-size: 20px;
    line-height: 27px;
    letter-spacing: 0.6px;
    white-space: nowrap;
  }
  .details .label {
    font-weight: 700;
    margin-right: 8px;
  }
</style>
</head>
<body>
  <div class="card">
    <div class="brand">
      <span class="brand-square"></span>
      <span class="brand-name">Tidewater Review</span>
    </div>
    <div class="contact-panel">
      <div class="person-name">Martin Kovar</div>
      <div class="person-title">CEO</div>
      <ul class="details">
        <li>Harbor Point Center, Lodni 12</li>
        <li>Brno - Czech Republic 602 00</li>
        <li><span class="label">p</span>+420 555 010 142</li>
        <li><span class="label">m</span>+420 555 010 058</li>
        <li><span class="label">USA</span>+1 555 014 7905</li>
        <li><span class="label">f</span>+420 555 010 200</li>
        <li><span class="label">e</span>martink@tidewaterreview.net</li>
        <li><span class="label">w</span>www.tidewaterreview.net</li>
      </ul>
    </div>
  </div>
</body>
</html>
```